Beauty Therapy Web Design

I need a web page design for a small beauty therapy clinic, the owner is currently the only beauty therapist working there.
We require the following pages:
Home
About
Treatments
Nails
Courses
Contact
I will attach the clinics business card, treatment menu and signage so that you get a feeling for the branding colours etc.
This is the first website for the beauty therapist, she would like to attract new clients and also tourists that come in on the cruise ships. The thing that sets her apart from other clinics is that she welcomes texting for appointments.
I have selected refundable because I have never done this before so I don't know what to expect, I have the full intention of going through with it as long as I get a good design.
Feel free to ask for further information
Reason: Project extended as I am away for work and am unable to meet with the owner.
Target Market(s)
Females 18 to 50
Industry/Entity Type
Business
Look and feel

```html
<!DOCTYPE html>
<html lang="en">
<head>
<meta charset="utf-8">
<title>Lumina Beauty Therapy Salon</title>
<link rel="stylesheet" href="https://fonts.googleapis.com/css2?family=Great+Vibes&family=Kalam:wght@700&family=Open+Sans:wght@400;600&family=Sofia&display=swap">
<style>
:root{
  --pink-hot:#ff5fd2;
  --magenta:#e0157f;
  --purple:#9b1fa8;
  --lilac:#e6dff0;
  --lilac-panel:#eab8ee;
  --body-ink:#4a4a4a;
  --yellow:#f6e21a;
  --teal:#4fb3c9;
  --button-pink:#e03d9b;
}
*{box-sizing:border-box;margin:0;padding:0}
html,body{width:900px;height:1200px;overflow:hidden;background:#fff}
.page{position:absolute;left:13px;top:13px;width:874px;height:1174px;border:1px solid #888;
  background:linear-gradient(to bottom,var(--pink-hot) 0,#ffa8ea 150px,#ffc8f4 394px,var(--lilac) 394px,#ece8f2 100%);
  overflow:hidden}
.page>*{position:absolute}
.page::before{content:"";position:absolute;left:0;top:0;width:874px;height:394px;
  background:linear-gradient(to right,rgba(255,255,255,.55),rgba(255,255,255,0) 40%,rgba(255,255,255,.5) 70%,rgba(255,255,255,0))}
.brand-name{left:66px;top:40px;font:600 54px/1 "Open Sans",sans-serif;color:var(--purple)}
.tagline{left:226px;top:8px;font:32px "Great Vibes",cursive;color:#222;white-space:nowrap}
.phone{left:676px;top:20px;display:flex;align-items:center;gap:10px;font:19px "Sofia",cursive;color:#333;white-space:nowrap}
.search{left:640px;top:71px;width:224px;height:22px;border-radius:11px;background:#fff;border:1px solid #bbb;box-shadow:inset 0 1px 3px rgba(0,0,0,.3)}
.search svg{position:absolute;left:8px;top:4px}
.search span{position:absolute;right:4px;top:3px;width:48px;height:14px;border-radius:7px;background:#aaa;color:#fff;font:italic 9px "Open Sans",sans-serif;text-align:center;line-height:14px}
.main-nav{left:9px;top:100px;width:856px;height:74px;display:flex}
.main-nav a{flex:1;display:flex;align-items:center;justify-content:center;text-decoration:none;white-space:nowrap;
  font:700 25px "Kalam",cursive;color:#2b2b2b;background:linear-gradient(#fff,#f4e6f2);
  border:1px solid #d7b3d3;border-radius:8px;box-shadow:0 2px 4px rgba(0,0,0,.25)}
.hero{left:60px;top:164px;width:754px;height:262px;background:#fff;box-shadow:0 0 6px rgba(0,0,0,.3)}
.hero-photo{position:absolute;left:10px;top:10px;width:734px;height:240px;
  background:linear-gradient(120deg,#8fc0e6 0,#cfe1ef 30%,#e8b9a2 55%,#c98d74 80%,#7a4d3c 100%)}
.hero-caption{position:absolute;left:10px;top:212px;width:734px;height:38px;background:rgba(40,25,25,.82);
  color:#fff;font:27px "Great Vibes",cursive;padding-left:12px;line-height:38px;white-space:nowrap}
.hero-caption b{font-weight:400;color:var(--yellow);margin-left:8px}
.btn{position:absolute;color:#fff;font:600 18px "Open Sans",sans-serif;border-radius:8px;display:flex;align-items:center;justify-content:center;gap:8px;text-decoration:none;white-space:nowrap}
.btn-learn{left:584px;top:138px;width:147px;height:32px;background:linear-gradient(var(--teal),#2b8ea6)}
.btn-text{left:460px;top:174px;width:271px;height:32px;background:linear-gradient(#ff5fae,var(--button-pink))}
.carousel{left:60px;top:414px;width:754px;height:193px;background:linear-gradient(#cfcfd6,#ececf0 60%,#c4c4cc);border:1px solid #aaa;border-radius:6px}
.thumb{position:absolute;top:22px;width:222px;height:147px;background:#fff;border-radius:6px;padding:7px;box-shadow:0 2px 5px rgba(0,0,0,.35)}
.thumb div{width:100%;height:100%}
.arrow{position:absolute;top:82px}
.divider{height:2px;background:#b5b5bd}
.ornament{width:56px;height:16px;border-radius:8px;background:#8e8e96}
.welcome-title{left:63px;top:640px;font:400 44px "Great Vibes",cursive;color:var(--purple)}
.welcome-sub{left:303px;top:687px;font:22px "Great Vibes",cursive;color:#333}
.welcome-copy{left:63px;top:724px;width:440px;font-family:"Sofia",cursive;color:var(--body-ink)}
.welcome-copy p{margin-bottom:14px}
.lead{font-size:15px;line-height:22.6px}
.lead::first-letter,.note.first::first-letter{font-size:26px}
.note{font-size:11.5px;line-height:17px}
.rule-v{left:507px;top:747px;width:2px;height:267px;background:#999}
.services{left:564px;top:640px;width:247px;height:454px;border-radius:8px;border:1px solid #c9a0cc;
  background:linear-gradient(#f4c9f2,var(--lilac-panel))}
.services h2{position:absolute;left:14px;top:8px;font:400 35px "Open Sans",sans-serif;color:var(--magenta);white-space:nowrap}
.service-img{position:absolute;left:154px;width:73px;height:104px;border:1px solid #777}
.service-btn{position:absolute;left:5px;width:117px;height:28px;background:linear-gradient(#e56ed8,#b93fb8);
  color:#fff;font:17px "Open Sans",sans-serif;padding-left:5px;line-height:28px;border-radius:2px;white-space:nowrap}
.service-btn svg{position:absolute;right:6px;top:7px}
.more-btn{position:absolute;left:29px;top:422px;width:190px;height:25px;border-radius:6px;background:linear-gradient(#ff7fc4,#e7489e);
  color:#fff;font:18px "Open Sans",sans-serif;text-align:center;line-height:25px;white-space:nowrap}
.copyright{left:14px;top:1136px;font:14px "Open Sans",sans-serif;color:#111}
.foot-nav{right:18px;top:1133px;font:16px "Open Sans",sans-serif;color:#111;word-spacing:2px;white-space:nowrap}
</style>
</head>
<body>
<div class="page">
  <div class="brand-name">Lumina</div>
  <div class="tagline">Beauty Therapy Salon</div>
  <div class="phone">
    <svg width="26" height="32" viewBox="0 0 26 32" aria-hidden="true"><rect x="4" y="2" width="14" height="28" rx="3" transform="rotate(20 11 16)" fill="#cfd3d8" stroke="#777"/><rect x="8" y="6" width="7" height="8" transform="rotate(20 11 16)" fill="#7fb6e0"/></svg>
    <span>021-555-0147</span>
  </div>
  <div class="search">
    <svg width="12" height="12" viewBox="0 0 12 12" aria-hidden="true"><circle cx="5" cy="5" r="3.5" fill="none" stroke="#888" stroke-width="1.5"/><line x1="7.5" y1="7.5" x2="11" y2="11" stroke="#888" stroke-width="1.5"/></svg>
    <span>Search</span>
  </div>

  <nav class="main-nav">
    <a href="#">Home</a><a href="#">Treatments</a><a href="#">Courses</a><a href="#">Nails</a><a href="#">About Us</a><a href="#">Contact Us</a>
  </nav>

  <section class="hero">
    <div class="hero-photo" role="img" aria-label="Photo of a woman relaxing during a shoulder massage"></div>
    <a class="btn btn-learn" href="#">Learn More <svg width="12" height="12" viewBox="0 0 12 12"><path d="M2 1l8 5-8 5z" fill="#fff"/></svg></a>
    <a class="btn btn-text" href="#">Text Us For An Appointment <svg width="12" height="12" viewBox="0 0 12 12"><path d="M2 1l8 5-8 5z" fill="#fff"/></svg></a>
    <div class="hero-caption">Beautify Your Beauty With Your Beauty Experts at<b>Lumina</b></div>
  </section>

  <section class="carousel">
    <svg class="arrow" style="left:4px" width="24" height="30" viewBox="0 0 24 30" aria-hidden="true"><path d="M20 2L4 15l16 13" fill="none" stroke="#999" stroke-width="5"/></svg>
    <div class="thumb" style="left:33px"><div role="img" aria-label="Photo of a woman with flowers in her hair" style="background:linear-gradient(135deg,#b3a36a,#d98fa8 60%,#e8d7cf)"></div></div>
    <div class="thumb" style="left:263px"><div role="img" aria-label="Photo of a woman receiving a facial treatment" style="background:linear-gradient(135deg,#8a6a55,#e7c4ad 50%,#f4f1ee)"></div></div>
    <div class="thumb" style="left:495px"><div role="img" aria-label="Photo of pedicured feet with orchid petals" style="background:linear-gradient(135deg,#f0e3ea,#e8b9a4 50%,#c98ab8)"></div></div>
    <svg class="arrow" style="left:726px" width="24" height="30" viewBox="0 0 24 30" aria-hidden="true"><path d="M4 2l16 13L4 28" fill="none" stroke="#999" stroke-width="5"/></svg>
  </section>

  <div class="divider" style="left:60px;top:627px;width:754px"></div>
  <div class="ornament" role="img" aria-label="Small floral ornament" style="left:408px;top:619px"></div>

  <h1 class="welcome-title">Welcome To Lumina</h1>
  <div class="welcome-sub">Beauty Therapy Saloon</div>
  <div class="welcome-copy">
    <p class="lead">Our Salon both belives and provides the Ultimate treatments in Skin Health and Beauty. Indulge and pamper yourself with our extensive range of facials, Body treatments, massage and of course the all important nail cure, specilised Waxing and general Waxing and Eye Care. At Lumina We truely love and Passion for the beauty Industry and we Hope you try this at Lumina.</p>
    <p class="note first">At Lumina you will experience the Ultimate in all things beauty. Our Salon Invites you to Indulge and pamper yourself with our extensive rane of services including specilalized waxing, Skin rejuvenation, facials, nails and eye treatments.</p>
    <p class="note">Our dedicated friendly therapist and technicians will ensure you experience the<br>Ultimate in all thing beaut.</p>
    <p class="note">So go on Treat yourself U deserved it...</p>
  </div>
  <div class="rule-v"></div>

  <aside class="services">
    <h2>Our Services</h2>
    <div class="service-img" style="top:52px;background:linear-gradient(#fff,#f0d2c0 60%,#f2a3b8)" role="img" aria-label="Photo of smooth waxed legs with a flower"></div>
    <div class="service-btn" style="top:130px">Waxing<svg width="14" height="14" viewBox="0 0 14 14"><path d="M3 1l8 6-8 6z" fill="#fff"/></svg></div>
    <div class="service-img" style="top:166px;background:linear-gradient(#7a5a48,#d8a584 50%,#b98366)" role="img" aria-label="Photo of a woman showing a spray tan"></div>
    <div class="service-btn" style="top:243px">Spray Tans<svg width="14" height="14" viewBox="0 0 14 14"><path d="M3 1l8 6-8 6z" fill="#fff"/></svg></div>
    <div class="service-img" style="top:280px;background:linear-gradient(#4a3a33,#e5c6b4 55%,#f1e4dc)" role="img" aria-label="Photo of a woman with glowing skin after a facial"></div>
    <div class="service-btn" style="top:352px">Facial<svg width="14" height="14" viewBox="0 0 14 14"><path d="M3 1l8 6-8 6z" fill="#fff"/></svg></div>
    <div class="more-btn">More Click Here &gt;&gt;&gt;</div>
  </aside>

  <div class="divider" style="left:84px;top:1104px;width:710px"></div>
  <div class="ornament" role="img" aria-label="Small floral ornament" style="left:408px;top:1096px"></div>

  <div class="copyright">Copyright © Fernleaf Web 2012</div>
  <nav class="foot-nav">Home &nbsp;|&nbsp; About &nbsp;|&nbsp; Nails &nbsp;|&nbsp; Treatment &nbsp;|&nbsp; Courses &nbsp;|&nbsp; Contact Us</nav>
</div>
</body>
</html>
```